Volbrey Inc Business Card

Looking to get an updated business card for a Contract Machining company (www.volbreyinc.example) - looking for a clean design the portrays the technical nature of the business - colors can follow the website design and be in any combination that makes sense (red black, white, metallic or silver) - logos attached for use also. Would like space for: Name, title, business phone (555 214-3086), cell phone , website (www.volbreyinc.example) - possibly QR code could be integrated for website (designer choice), business address - 418 Harlow Bend, Ashwick Falls, XY 48199 (cards will be for 4 employees, I will either need to modify a template or I can provide individual information)
Target Market(s)
Aerospace, defense and medical device manufacturing companies that need machining
Industry/Entity Type
Machining for aerospace, defense, medical
Contact Information for Business Card
Name, Title, Business Phone, Cell Phone, email, business website and business address
Look and feel

```html
<!DOCTYPE html>
<html lang="en">
<head>
<meta charset="utf-8">
<title>Volbrey Inc Business Card</title>
<link href="https://fonts.googleapis.com/css2?family=Montserrat:wght@700;800&family=Arimo:wght@400;700&display=swap" rel="stylesheet">
<style>
  :root {
    --backdrop: #d9d9d9;
    --brand-red: #b31c22;
    --card-white: #ffffff;
    --divider-grey: #7a7a7a;
    --card-black: #232323;
    --pattern-grey: #3a3a3a;
    --ink-light: #ffffff;
  }
  * { box-sizing: border-box; margin: 0; padding: 0; }
  html, body { width: 1200px; height: 874px; overflow: hidden; }
  body {
    background: var(--backdrop);
    font-family: "Arimo", Arial, sans-serif;
    position: relative;
  }
  .card {
    position: absolute;
    left: 280px;
    width: 640px;
    height: 366px;
    border-radius: 22px;
    overflow: hidden;
    box-shadow: 0 10px 24px rgba(0,0,0,.25);
  }
  /* Back side */
  .card-back { top: 46px; background: var(--card-black); }
  .back-pattern {
    position: absolute; inset: 0;
    background: linear-gradient(115deg, #1c1c1c 0%, var(--card-black) 45%, var(--pattern-grey) 100%);
  }
  .back-brand {
    position: absolute; right: 120px; bottom: 44px;
    display: flex; flex-direction: column; align-items: center; gap: 8px;
  }
  .back-brand .brand-dot { width: 84px; height: 84px; border-radius: 50%; background: var(--brand-red); }
  .back-brand .brand-name { font-size: 20px; }
  .brand-name {
    font-family: "Montserrat", Arial, sans-serif;
    font-weight: 800;
    color: var(--brand-red);
    letter-spacing: 1px;
    white-space: nowrap;
  }
  /* Front side */
  .card-front { top: 460px; background: var(--card-white); display: flex; }
  .front-brand {
    width: 292px;
    display: flex; flex-direction: column; align-items: center; justify-content: center; gap: 14px;
  }
  .front-brand .brand-dot { width: 158px; height: 158px; border-radius: 50%; background: var(--brand-red); }
  .front-brand .brand-name { font-size: 34px; }
  .divider { width: 10px; background: var(--divider-grey); }
  .front-details {
    flex: 1;
    background: var(--brand-red);
    color: var(--ink-light);
    padding: 58px 30px 0 44px;
  }
  .person-name { font-weight: 700; font-size: 27px; line-height: 1; }
  .person-title { font-size: 16px; margin-top: 4px; }
  .address { font-size: 17px; line-height: 1.3; margin-top: 24px; }
  .contact-list { list-style: none; margin-top: 14px; font-size: 17px; line-height: 1.35; }
  .contact-list li { display: flex; align-items: center; gap: 10px; }
  .contact-list svg { width: 14px; height: 14px; flex: none; fill: var(--ink-light); }
</style>
</head>
<body>

<section class="card card-back">
  <div class="back-pattern" role="img" aria-label="Dark embossed repeating brand pattern"></div>
  <div class="back-brand">
    <span class="brand-dot"></span>
    <span class="brand-name">VOLBREY INC</span>
  </div>
</section>

<section class="card card-front">
  <div class="front-brand">
    <span class="brand-dot"></span>
    <span class="brand-name">VOLBREY INC</span>
  </div>
  <div class="divider"></div>
  <div class="front-details">
    <p class="person-name">Daniel Porter</p>
    <p class="person-title">President</p>
    <p class="address">418 Harlow Bend<br>Ashwick Falls, XY 48199</p>
    <ul class="contact-list">
      <li><svg viewBox="0 0 16 16"><path d="M3 1l3 3-1.5 2a9 9 0 0 0 5.5 5.5L12 10l3 3-2 2C7 15 1 9 1 3z"/></svg>555 214-3086</li>
      <li><svg viewBox="0 0 16 16"><path d="M4 0h8a1 1 0 0 1 1 1v14a1 1 0 0 1-1 1H4a1 1 0 0 1-1-1V1a1 1 0 0 1 1-1zm1 2v10h6V2z"/></svg>555 830-4172</li>
      <li><svg viewBox="0 0 16 16"><path d="M0 3h16v10H0zm1.5 1.5L8 9l6.5-4.5V4h-13z"/></svg>info@volbreyinc.example</li>
      <li><svg viewBox="0 0 16 16"><circle cx="8" cy="8" r="7"/></svg>www.volbreyinc.example</li>
    </ul>
  </div>
</section>

</body>
</html>
```